Stationery Design Project for Nimbora, Chicago

Nimbora, a street parking application which helps car drivers find a street parking spot by offering an ideal path along which to look for parking. This path is calculated by our algorithm based on data (e.g. historical data, baseball games schedule, etc.). Along this path the driver will find a spot and will also save 70% of the search time. Customer we target is reg. between 21 and 45 yo.

We envision something young, fresh, bright and original. Slightly abstract maybe. It should represent the idea and elements of finding street parking in the city, e.g. car(s), parking spot, people, city, etc. (just ideas!).

Logo is attached.

Requirement:
- Business Cards (2 Sided Full Color CMYK)
- Letterhead (1 Sided Full Color CMYK)
- Envelope (1 Sided Full Color CMYK)
- Sticker (1 Sided Full Color CMYK), round with a 2inch diameter.

Reason: We're starting to get more and more designs and need more time to look into all of them. Very exciting!! Thanks to everybody!

Hi all, we're in the process of selecting our favs. Though choices!!! Really good submissions. Will keep you posted and sorry for the delay.

Target Market(s)

Car drivers and owners between 21 and 45

Industry/Entity Type

Parking

Requirements
Must have
• Sticker should be round and include company URL nimbora.com and the new logo which we will attach soon.
Should not have
• Should not be too serious or boring.

```html
<!DOCTYPE html>
<html lang="en">
<head>
<meta charset="utf-8">
<title>Nimbora Business Card</title>
<link rel="stylesheet" href="https://fonts.googleapis.com/css2?family=Open+Sans:wght@400;600;700&display=swap">
<style>
  :root {
    --backdrop: #d9d9d9;
    --card: #ffffff;
    --ink-dark: #1f1f1f;
    --ink-gray: #555555;
    --ink-soft: #5e5e5e;
    --brand-blue: #1f4fc2;
    --brand-blue-light: #3a86e0;
    --road-light: #8c8a84;
    --road-dark: #55544f;
    --car-red: #c9434a;
    --car-blue: #2c3466;
    --car-silver: #c4c6c8;
  }
  * { margin: 0; padding: 0; box-sizing: border-box; }
  html, body {
    width: 956px; height: 1200px; overflow: hidden;
    background: var(--backdrop);
    font-family: "Open Sans", Arial, sans-serif;
  }
  .stage { position: relative; width: 956px; height: 1200px; }

  .card {
    position: absolute; left: 74px; width: 798px;
    background: var(--card); border-radius: 28px; overflow: hidden;
    box-shadow: 0 4px 10px rgba(0,0,0,0.25);
  }
  .card--front { top: 110px; height: 456px; }
  .card--back { top: 648px; height: 460px; }

  .brand-name {
    position: absolute; font-weight: 600; color: var(--ink-dark);
    letter-spacing: 0; line-height: 1;
  }
  .card--front .brand-name { left: 472px; top: 34px; font-size: 70px; }

  .brand-dot {
    position: absolute; border-radius: 50%;
    background: radial-gradient(circle at 40% 35%, var(--brand-blue-light), var(--brand-blue) 70%);
  }
  .card--front .brand-dot { left: 92px; top: 50px; width: 252px; height: 252px; }

  .person { position: absolute; left: 473px; top: 208px; color: var(--ink-gray); }
  .person__name { font-size: 24px; font-weight: 700; line-height: 1.3; }
  .person__role { font-size: 19px; font-weight: 700; line-height: 1.3; }

  .contact-list { position: absolute; left: 470px; top: 296px; list-style: none; }
  .contact-list li {
    display: flex; align-items: center; height: 32px;
    font-size: 20px; color: var(--ink-soft);
  }
  .contact-list svg { width: 20px; height: 20px; margin-right: 14px; fill: var(--ink-soft); }

  .address {
    position: absolute; left: 0; width: 434px; top: 372px;
    text-align: center; font-size: 19px; line-height: 28px; color: var(--ink-soft);
  }

  .back-brand { position: absolute; left: 174px; top: 30px; height: 130px; width: 540px; }
  .card--back .brand-dot { left: 0; top: 0; width: 128px; height: 128px; }
  .card--back .brand-name { left: 150px; top: 20px; font-size: 84px; }

  .web-line {
    position: absolute; left: 0; width: 100%; top: 210px;
    text-align: center; font-size: 19px; color: var(--ink-soft);
  }
  .web-line b { color: var(--ink-dark); }
  .web-line .sep { margin: 0 10px; }

  .street-photo {
    position: absolute; left: 0; bottom: 0; width: 100%; height: 208px;
    background:
      radial-gradient(ellipse 130px 55px at 555px 40px, rgba(201,67,74,0.85), rgba(201,67,74,0) 100%),
      radial-gradient(ellipse 140px 55px at 620px 125px, rgba(44,52,102,0.85), rgba(44,52,102,0) 100%),
      radial-gradient(ellipse 120px 70px at 380px 130px, rgba(196,198,200,0.8), rgba(196,198,200,0) 100%),
      linear-gradient(180deg, var(--road-light), var(--road-dark));
  }
</style>
</head>
<body>
<div class="stage">

  <section class="card card--front">
    <div class="brand-dot"></div>
    <div class="brand-name">nimbora</div>

    <div class="person">
      <div class="person__name">Your Name</div>
      <div class="person__role">Designation</div>
    </div>

    <ul class="contact-list">
      <li><svg viewBox="0 0 20 20"><path d="M2 7c0-2 3-3 8-3s8 1 8 3v2h-4V7H6v2H2z"/><rect x="4" y="10" width="12" height="7" rx="1"/></svg>123-456-7890</li>
      <li><svg viewBox="0 0 20 20"><rect x="5" y="2" width="10" height="5"/><rect x="1" y="8" width="18" height="7" rx="1"/><rect x="5" y="13" width="10" height="5"/></svg>123-456-7890</li>
      <li><svg viewBox="0 0 20 20"><path d="M2 6h16v11H2z M2 6l8 6 8-6" fill="none" stroke="#5e5e5e" stroke-width="1.6"/></svg>name@website.com</li>
      <li><svg viewBox="0 0 20 20"><circle cx="10" cy="10" r="7"/></svg>www.website.com</li>
    </ul>

    <div class="address">City Name, Street Name<br>State Name, Country Code</div>
  </section>

  <section class="card card--back">
    <div class="back-brand">
      <div class="brand-dot"></div>
      <div class="brand-name">nimbora</div>
    </div>

    <p class="web-line"><b>e</b> : name@website.com<span class="sep">|</span><b>w</b> : www.website.com</p>

    <div class="street-photo" role="img" aria-label="Overhead photo of a red, a silver and a blue car in marked street parking bays beside a cyclist"></div>
  </section>

</div>
</body>
</html>
```